Business Cards for a law firm

Business cards for our law firm. Use our silhoette logo and OAK PARTNERS - check our website (www.oakpartners.example)

Contact Information for Business Card

our silhouette logo, OAK PARTNERS, 800-555-0147, Dorian Pemberton, dorian@oakpartners.example

Requirements
Must have
• our silhouette logo, OAK PARTNERS, 800-555-0147, Dorian Pemberton, dorian@oakpartners.example

```html
<!DOCTYPE html>
<html lang="en">
<head>
<meta charset="utf-8">
<title>Oak Partners — Business Cards</title>
<link rel="stylesheet" href="https://fonts.googleapis.com/css2?family=Michroma&family=Poppins:wght@400;500&display=swap">
<style>
  :root {
    --navy: #1a3170;
    --navy-deep: #0f2359;
    --ink: #1e1f2b;
    --paper: #ffffff;
    --backdrop: #858585;
  }
  * { margin: 0; padding: 0; box-sizing: border-box; }
  html, body { width: 1093px; height: 1200px; overflow: hidden; }
  body { background: var(--backdrop); position: relative; font-family: "Poppins", sans-serif; }

  .card {
    position: absolute;
    left: 265px;
    width: 578px;
    height: 356px;
    border-radius: 24px;
    overflow: hidden;
  }
  .card--front { top: 226px; background: var(--paper); }
  .card--back  { top: 621px; background: var(--navy); }

  .brand {
    position: absolute;
    display: flex;
    align-items: center;
    gap: 14px;
  }
  .brand__dot {
    width: 36px; height: 36px; border-radius: 50%;
    background: var(--navy);
  }
  .brand__name {
    font-family: "Michroma", sans-serif;
    font-size: 21px;
    letter-spacing: 1.5px;
    color: var(--navy);
    white-space: nowrap;
  }
  .card--front .brand { top: 72px; right: 32px; }
  .card--back .brand { top: 157px; left: 50%; transform: translateX(-50%); }
  .card--back .brand__dot { width: 40px; height: 40px; background: var(--navy-deep); }
  .card--back .brand__name { color: var(--navy-deep); font-size: 24px; }

  .holder {
    position: absolute; left: 26px; top: 203px;
    font-family: "Michroma", sans-serif;
    font-size: 17px;
    color: var(--navy);
    letter-spacing: 0.3px;
  }
  .divider {
    position: absolute; left: 26px; right: 32px; top: 239px;
    height: 1px; background: var(--navy);
  }
  .contact {
    position: absolute; left: 26px; top: 259px;
    list-style: none;
  }
  .contact__item { display: flex; align-items: center; gap: 6px; height: 28px; }
  .contact__icon { width: 25px; height: 25px; flex: none; }
  .contact__phone { font-size: 22px; font-weight: 500; color: var(--navy); letter-spacing: -0.3px; }
  .contact__email { font-size: 16px; color: var(--ink); }
  .website {
    position: absolute; right: 31px; top: 291px;
    font-size: 16px; color: var(--ink);
  }
  .website__domain { color: var(--navy); font-weight: 500; }
  .front-band {
    position: absolute; left: 0; right: 0; bottom: 0; height: 16px;
    background: var(--navy);
  }
</style>
</head>
<body>
  <section class="card card--front" aria-label="Business card front">
    <div class="brand">
      <span class="brand__dot"></span>
      <span class="brand__name">OAK PARTNERS</span>
    </div>
    <h1 class="holder">DORIAN PEMBERTON</h1>
    <div class="divider"></div>
    <ul class="contact">
      <li class="contact__item">
        <svg class="contact__icon" viewBox="0 0 25 25" aria-hidden="true">
          <circle cx="12.5" cy="12.5" r="11.5" fill="none" stroke="#1a3170" stroke-width="1.2"/>
          <path d="M9 7.5l2 2.2-1.1 1.4c.7 1.6 1.8 2.7 3.4 3.5l1.4-1.1 2.2 2-1.2 1.6c-3.8-.6-6.7-3.5-7.3-7.3z" fill="#1a3170"/>
        </svg>
        <span class="contact__phone">800-555-0147</span>
      </li>
      <li class="contact__item">
        <svg class="contact__icon" viewBox="0 0 25 25" aria-hidden="true">
          <circle cx="12.5" cy="12.5" r="11.5" fill="none" stroke="#1a3170" stroke-width="1.2"/>
          <rect x="7" y="9" width="11" height="7.5" fill="#1a3170"/>
          <path d="M7 9l5.5 4.2L18 9" fill="none" stroke="#fff" stroke-width="0.9"/>
        </svg>
        <span class="contact__email">dorian@oakpartners.example</span>
      </li>
    </ul>
    <p class="website">www.<span class="website__domain">oakpartners</span>.example</p>
    <div class="front-band"></div>
  </section>

  <section class="card card--back" aria-label="Business card back">
    <div class="brand">
      <span class="brand__dot"></span>
      <span class="brand__name">OAK PARTNERS</span>
    </div>
  </section>
</body>
</html>
```